New Business card design to reflect rebrand

I would like a business card design with a good base colour for our new logo and also a placeholder for a profile pic of the card holder. the design needs to be editable to the point that we can easily change the picture of the person and use that design for printmerlo etc. we are looking at a metalic finish business card so will need a good base colour to bring out the finish.

Target Market(s)

prospective customers

Industry/Entity Type

Business

Contact Information for Business Card

I would like one editable design that we can change the name of the card holder and profile picture. The design need to be in a format that be send to printmerlo etc.

Our address is Fenwick Lodge, Copse Lane, Ashcombe Vale, GU14 3TP Tel no. 01483 556172

Requirements
Must have
• place holder for a profile pic for the card holder. in AI or preferably PSD format

```html
<!DOCTYPE html>
<html lang="en">
<head>
<meta charset="utf-8">
<title>Larkfield Workplace Services – Business Card</title>
<link href="https://fonts.googleapis.com/css2?family=Montserrat:wght@500;600;700&family=Open+Sans:wght@400;600&display=swap" rel="stylesheet">
<style>
  :root {
    --slate: #42566f;
    --orange: #ee6a0f;
    --white: #ffffff;
    --ink: #1f1f1f;
    --stage: #ecebe8;
    --photo-top: #c9cfd6;
    --photo-bottom: #3b4250;
  }
  * { margin: 0; padding: 0; box-sizing: border-box; }
  html, body { width: 1200px; height: 900px; overflow: hidden; }
  body {
    background: var(--stage);
    position: relative;
    font-family: "Open Sans", Arial, sans-serif;
  }
  .card {
    position: absolute;
    width: 580px;
    height: 360px;
    overflow: hidden;
    box-shadow: 0 6px 18px rgba(0,0,0,0.18);
  }

  /* Front */
  .card-front { left: 70px; top: 50px; background: var(--white); }
  .profile-photo {
    position: absolute;
    left: 0; top: 18px;
    width: 280px; height: 270px;
    background: linear-gradient(180deg, var(--photo-top) 0%, #8a93a0 55%, var(--photo-bottom) 100%);
  }
  .front-band {
    position: absolute;
    left: 0; bottom: 0;
    width: 580px; height: 100px;
  }
  .brand-name {
    position: absolute;
    right: 32px; top: 50px;
    font-family: "Montserrat", Arial, sans-serif;
    font-weight: 700;
    font-size: 44px;
    color: var(--slate);
    letter-spacing: 1px;
  }
  .holder-name {
    position: absolute;
    right: 32px; top: 152px;
    font-family: "Montserrat", Arial, sans-serif;
    font-weight: 500;
    font-size: 20px;
    letter-spacing: 1.5px;
    text-transform: uppercase;
    color: var(--orange);
  }
  .holder-name .surname { color: var(--slate); }
  .contact-list {
    position: absolute;
    right: 32px; top: 200px;
    list-style: none;
    text-align: right;
    font-size: 15px;
    color: var(--ink);
    line-height: 24px;
  }
  .contact-list li { display: flex; justify-content: flex-end; align-items: center; gap: 10px; }
  .contact-list svg { width: 11px; height: 11px; fill: var(--orange); }
  .address {
    position: absolute;
    left: 0; bottom: 26px;
    width: 580px;
    text-align: center;
    color: var(--white);
    font-size: 15px;
  }

  /* Back */
  .card-back {
    left: 560px; top: 480px;
    background: var(--orange);
    display: flex;
    flex-direction: column;
    align-items: center;
    justify-content: center;
    color: var(--white);
    font-family: "Montserrat", Arial, sans-serif;
  }
  .back-brand {
    font-weight: 700;
    font-size: 54px;
    letter-spacing: 2px;
    text-transform: uppercase;
  }
  .back-tagline {
    margin-top: 6px;
    font-weight: 500;
    font-size: 19px;
    letter-spacing: 4px;
    text-transform: uppercase;
  }
</style>
</head>
<body>

  <section class="card card-front">
    <div class="profile-photo" role="img" aria-label="Profile photo of the card holder"></div>

    <svg class="front-band" viewBox="0 0 580 100" aria-hidden="true">
      <polygon points="272,8 342,8 330,28 272,28" fill="var(--orange)"/>
      <polygon points="0,28 330,28 352,0 580,0 580,100 0,100" fill="var(--slate)"/>
    </svg>

    <div class="brand-name">Larkfield</div>
    <div class="holder-name">Marcus <span class="surname">Reed</span></div>

    <ul class="contact-list">
      <li>01483 556172
        <svg viewBox="0 0 24 24"><path d="M6.6 10.8a15.1 15.1 0 0 0 6.6 6.6l2.2-2.2a1 1 0 0 1 1-.25 11.4 11.4 0 0 0 3.6.57 1 1 0 0 1 1 1V20a1 1 0 0 1-1 1A17 17 0 0 1 3 4a1 1 0 0 1 1-1h3.5a1 1 0 0 1 1 1c0 1.250.2 2.450.57 3.57a1 1 0 0 1-.25 1z"/></svg>
      </li>
      <li>info@larkfieldws.com
        <svg viewBox="0 0 24 24"><path d="M2 5h20v14H2z M2 5l10 8 10-8" fill="var(--orange)" stroke="var(--white)" stroke-width="1.5"/></svg>
      </li>
    </ul>

    <p class="address">Fenwick Lodge, Copse Lane, Ashcombe Vale, GU14 3TP</p>
  </section>

  <section class="card card-back">
    <div class="back-brand">Larkfield</div>
    <div class="back-tagline">Workplace Services</div>
  </section>

</body>
</html>
```